2 x Digitize Logo | 2 x Business Cards | 2 x Fridge Magnets

We require 6 deliverables:
1. Residential logo redrawn (same just high quality for large print format).
2. Corporate logo redrawn (minor changes to wording and high quality for large print format).
3. New business card design for Furniture Removals (residential)
4. New business card design for Corporate Relocations (business)
5. New Fridge magnet for Furniture removals (residential)
6. New fridge magnet for Corporate Relocations (business)
1. Residential Logo
a. We require the logo to be translated into a high quality digital image with no modifications.
(see attached resilogo.jpg)
2. Residential Logo
a. We require the logo to be edited (add the word corporate relocations) be translated into a high quality digital image.
(see attached corplogo.jpg)
3. Using the resilogo please make a new business card for our business.
a. Please see the web site https://www.larkbendcarters.com.au for colours and inspiration.
b. The residential business card needs the following information:
i. Business Name (using the residential logo).
ii. Free Call: 1800 LB Cart (the L, B and Cart much be the same colour as the logo).
iii. Website: www.LarkbendCarters.com.au
iv. Address: 4/17 Ormsdale Court, VIC 3264
v. Email: cart@LarkbendCarters.com.au
vi. backof Card:
Review our service
www.PennantOrbit.com.au
Services: Local, Country, Interstate | Furniture Removals | Piano, Billiard Tables & Antiques
4. Using the corplogo please make a new business card for our business.
b. The corporate business card needs the following information:
i. Business Name (using the corporate logo).
v. Email: corporate@LarkbendCarters.com.au
vi. Back of Card:
Review our service
www.PennantOrbit.com.au
Services: Corporate relocations | Office equipment moves | Packing Service | Packing Materials
5. Using the resilogo please make a new fridge magent for our business.
b. The residential fidge magnet needs the following information:
iv. Services: Local, Country, Interstate | Furniture Removals | Piano, Billiard Tables & Antiques
6. Using the corplogo please make a new fridge magent for our business.
b. The corporate fidge magnet needs the following information:
iv. Services: Local, Country, Interstate | Corporate relocations
Target Market(s)
Residential Furniture Removals and Corporate Office relocations
Industry/Entity Type
Business
Contact Information for Business Card
Please see full brief for six items required
Requirements
Must have
- Clean simple, easy to read
Nice to have
- fresh, stand out, eye catching
Should not have
- plain, standard, boring, general

```html
<!DOCTYPE html>
<html lang="en">
<head>
<meta charset="utf-8">
<title>Larkbend Carters – Corporate Relocations Business Card</title>
<link href="https://fonts.googleapis.com/css2?family=Open+Sans:wght@400;600&display=swap" rel="stylesheet">
<style>
  :root {
    --brand-red: #c0111b;
    --brand-green: #0a7a3d;
    --card-white: #ffffff;
    --card-black: #050505;
    --ink: #1a1a1a;
    --page-bg: #e9e6e1;
    --on-dark: #f2f2f2;
  }
  * { box-sizing: border-box; margin: 0; padding: 0; }
  html, body {
    width: 1200px; height: 900px; overflow: hidden;
    background: var(--page-bg);
    font-family: "Open Sans", Arial, sans-serif;
  }
  .sheet {
    width: 1200px; height: 900px;
    display: flex; flex-direction: column;
    align-items: center; justify-content: center; gap: 44px;
  }
  .card {
    position: relative;
    width: 600px; height: 367px;
    overflow: hidden;
    box-shadow: 0 6px 18px rgba(0,0,0,0.18);
  }

  /* Back of card */
  .card--back { background: var(--card-black); color: var(--on-dark); }
  .review { position: absolute; left: 52px; top: 44px; font-size: 15px; line-height: 1.55; }
  .review__title { text-transform: uppercase; letter-spacing: 0.3px; }
  .review__link { color: var(--on-dark); text-decoration: none; }
  .back-name {
    position: absolute; right: 48px; top: 92px; text-align: right;
    font-weight: 600; font-size: 24px; text-transform: uppercase;
    color: var(--brand-red); line-height: 1.15;
  }
  .back-name__tag { display: block; font-weight: 400; font-size: 17px; color: var(--brand-green); }
  .services { position: absolute; left: 90px; top: 222px; font-size: 16px; line-height: 1.45; }
  .services__title { color: var(--brand-green); text-transform: uppercase; }
  .services__list { list-style: none; }
  .services__list li { position: relative; padding-left: 20px; }
  .services__list li::before {
    content: ""; position: absolute; left: 2px; top: 8px;
    width: 9px; height: 9px; border-radius: 50%; background: var(--brand-red);
  }

  /* Front of card */
  .card--front { background: var(--card-white); color: var(--ink); }
  .front-name { position: absolute; left: 56px; top: 46px; text-transform: uppercase; }
  .front-name__title { font-weight: 600; font-size: 30px; color: var(--brand-red); letter-spacing: 0.5px; }
  .front-name__tag { font-weight: 400; font-size: 29px; color: var(--brand-green); line-height: 1.1; }
  .contacts { position: absolute; left: 70px; top: 160px; list-style: none; font-size: 18px; line-height: 1.75; }
  .contacts li { display: flex; align-items: center; gap: 10px; }
  .contacts svg { width: 16px; height: 16px; fill: var(--brand-green); flex: none; }
  .contacts a { color: inherit; text-decoration: none; }
  .accent { color: var(--brand-red); }
  .front-bands { position: absolute; inset: 0; width: 600px; height: 367px; }
  .band--red { fill: var(--brand-red); }
  .band--green { fill: var(--brand-green); }
</style>
</head>
<body>
<main class="sheet">

  <section class="card card--back" aria-label="Back of business card">
    <div class="review">
      <p class="review__title">Review our service</p>
      <a class="review__link" href="https://www.pennantorbit.com.au">www.PennantOrbit.com.au</a>
    </div>
    <p class="back-name">Larkbend Carters<span class="back-name__tag">Corporate Relocations</span></p>
    <div class="services">
      <p class="services__title">Services:</p>
      <ul class="services__list">
        <li>Corporate relocations</li>
        <li>Office equipment moves</li>
        <li>Packing Service</li>
        <li>Packing Materials</li>
      </ul>
    </div>
  </section>

  <section class="card card--front" aria-label="Front of business card">
    <svg class="front-bands" viewBox="0 0 600 367" aria-hidden="true">
      <polygon class="band--red" points="0,348 300,348 600,100 600,205 420,367 0,367"/>
      <polygon class="band--green" points="480,367 600,255 600,367"/>
    </svg>
    <div class="front-name">
      <p class="front-name__title">Larkbend Carters</p>
      <p class="front-name__tag">Corporate Relocations</p>
    </div>
    <ul class="contacts">
      <li>
        <svg viewBox="0 0 24 24"><path d="M6.6 10.8a15.1 15.1 0 0 0 6.6 6.6l2.2-2.2a1 1 0 0 1 1-.25 11.4 11.4 0 0 0 3.6.57 1 1 0 0 1 1 1V20a1 1 0 0 1-1 1A17 17 0 0 1 3 4a1 1 0 0 1 1-1h3.5a1 1 0 0 1 1 1c0 1.25.2 2.45.57 3.57a1 1 0 0 1-.25 1z"/></svg>
        <span>1800 <span class="accent">LB</span> <span class="accent">Cart</span></span>
      </li>
      <li>
        <svg viewBox="0 0 24 24"><path d="M2 5h20v14H2zm2 2v.5l8 5 8-5V7zm0 2.8V17h16V9.8l-8 5z"/></svg>
        <a href="mailto:cart@LarkbendCarters.com.au">cart@LarkbendCarters.com.au</a>
      </li>
      <li>
        <svg viewBox="0 0 24 24"><path d="M12 2a10 10 0 1 0 0 20 10 10 0 0 0 0-20zm6.9 9h-3a15 15 0 0 0-1.3-5.6A8 8 0 0 1 18.9 11zM12 4.1c.9 1.3 1.7 3.7 1.9 6.9h-3.8c.2-3.2 1-5.6 1.9-6.9zM5.1 13h3a15 15 0 0 0 1.3 5.6A8 8 0 0 1 5.1 13zm3-2h-3a8 8 0 0 1 4.3-5.6A15 15 0 0 0 8.1 11zM12 19.9c-.9-1.3-1.7-3.7-1.9-6.9h3.8c-.2 3.2-1 5.6-1.9 6.9zm2.6-1.3a15 15 0 0 0 1.3-5.6h3a8 8 0 0 1-4.3 5.6z"/></svg>
        <a href="https://www.larkbendcarters.com.au">www.LarkbendCarters.com.au</a>
      </li>
      <li>
        <svg viewBox="0 0 24 24"><path d="M12 2a7 7 0 0 0-7 7c0 5.2 7 13 7 13s7-7.8 7-13a7 7 0 0 0-7-7zm0 9.5A2.5 2.5 0 1 1 12 6.5a2.5 2.5 0 0 1 0 5z"/></svg>
        <span>4/17 Ormsdale Court, VIC 3264</span>
      </li>
    </ul>
  </section>

</main>
</body>
</html>
```